Ecommerce site that acts also as a portal for B2C members and non- members and B2B. Please see attachment this is for only front end work, backend will follow. Husk and Kettle- a MRVL Hospitality Company

Products
Coffee bean sourcing, acquisition, roasting, grinding, blending, sale/delivery
Tea sourcing, acquisition, roasting, grinding, blending, sale/delivery
Applicable/Associated Merchandise and Accoutrements

Initial market penetration for both B2C and B2B offering Husk and Kettle custom blends of both Coffees and Teas.
B2C- Zelvora style sale/distribution via guest and members. Members initial fee $129 annual $99 a year thereafter with benefits such as 1st year gift of a French Press Travel Mug (customized/logo/name/brand), monthly samples. Attached document has non project related information for narrative and conceptual inputs.

Coding

```html
<!DOCTYPE html>
<html lang="en">
<head>
<meta charset="utf-8">
<title>Husk and Kettle — Artisan Coffee &amp; Tea</title>
<link href="https://fonts.googleapis.com/css2?family=Playfair+Display:wght@400;500&family=Poppins:wght@400;500;600&display=swap" rel="stylesheet">
<style>
:root{
  --ink:#0f0a06;
  --ink-2:#1a110a;
  --brown-deep:#2a1a0e;
  --gold:#c08a45;
  --gold-2:#a5662a;
  --gold-3:#6e3d14;
  --cream:#f3e8da;
  --text-light:#f1ece6;
  --text-muted:#cfc5ba;
  --line:#4a3726;
  --white:#ffffff;
  --dark-text:#1d1510;
  --serif:"Playfair Display", Georgia, serif;
  --sans:"Poppins", Arial, sans-serif;
}
*{box-sizing:border-box;margin:0;padding:0}
html,body{width:1200px;height:3906px;overflow:hidden}
body{position:relative;background:var(--white);font-family:var(--sans);color:var(--text-light)}
.abs{position:absolute}
.center{left:0;width:1200px;text-align:center}
.h-serif{font-family:var(--serif);font-weight:400;text-transform:uppercase;letter-spacing:.3px}
.btn{position:absolute;display:flex;align-items:center;justify-content:center;height:27px;border-radius:14px;
  background:linear-gradient(90deg,var(--gold-2),var(--gold-3));color:var(--white);font-size:9px;font-weight:600;letter-spacing:.3px;text-transform:uppercase}
.photo{position:absolute;display:block}

/* dark upper band */
.dark-top{position:absolute;left:0;top:0;width:1200px;height:1863px;
  background:radial-gradient(ellipse 420px 520px at 1200px 1250px,#4a2c12 0%,transparent 70%),var(--ink)}

/* header */
.nav a{position:absolute;top:26px;font-size:10px;color:var(--text-light);text-decoration:none}
.brand{position:absolute;left:540px;top:8px;width:120px;text-align:center}
.brand-dot{width:26px;height:26px;border-radius:50%;background:var(--gold-2);margin:0 auto 3px}
.brand-name{font-family:var(--serif);font-size:14px;line-height:14px;color:var(--gold);text-transform:uppercase}
.nav-icons{position:absolute;left:990px;top:25px;display:flex;gap:10px}

/* hero */
.hero-photo{left:0;top:95px;width:1200px;height:665px;
  background:radial-gradient(ellipse 260px 170px at 600px 460px,#d7cfc4 0%,#8a6a4d 35%,transparent 70%),
             radial-gradient(ellipse 420px 300px at 180px 430px,#5a2f14 0%,transparent 70%),
             radial-gradient(ellipse 360px 300px at 1050px 460px,#5a3016 0%,transparent 70%),
             linear-gradient(180deg,#1a100a 0%,#2c1a0e 50%,var(--ink) 100%)}
.hero-title{top:162px;font-size:32px;color:var(--cream)}
.hero-sub{top:206px;font-size:10px;line-height:16px;color:var(--text-light)}

/* products */
.sec-title{font-size:32px}
.card{position:absolute;top:897px;width:220px;height:288px;border:1px solid var(--line);border-radius:10px;background:#150e08;text-align:center}
.card .photo{left:8px;top:7px;width:204px;height:137px;border-radius:4px}
.card h3{position:absolute;left:0;width:100%;top:166px;font-family:var(--serif);font-weight:400;font-size:15px;color:var(--cream);text-transform:uppercase}
.card p{position:absolute;left:22px;width:176px;top:193px;font-size:9.5px;line-height:16px;color:var(--text-light)}
.card .btn{left:60px;top:245px;width:100px}

/* blend steps */
.step{position:absolute;width:170px;text-align:center}
.step-circle{width:88px;height:88px;border-radius:50%;margin:0 auto;background:radial-gradient(circle at 40% 35%,#b36b2a,var(--gold-3));position:relative}
.step-num{position:absolute;right:-8px;top:2px;width:24px;height:24px;border-radius:50%;background:var(--white);color:var(--dark-text);font-size:9px;display:flex;align-items:center;justify-content:center}
.step p{margin-top:10px;font-size:9.5px;line-height:16px;color:var(--text-light)}

/* wholesale */
.wholesale{left:147px;top:1652px;width:912px;height:291px;border-radius:30px;overflow:hidden;
  background:radial-gradient(ellipse 200px 120px at 200px 80px,#5a3a26,transparent 70%),radial-gradient(ellipse 240px 140px at 760px 230px,#4d3020,transparent 70%),linear-gradient(135deg,#2e1e14,#3d291c 50%,#24170f)}

/* insights */
.ins-card{position:absolute;top:2113px;width:283px;height:302px;border-radius:8px;overflow:hidden}
.ins-card h3{position:absolute;left:33px;font-family:var(--serif);font-weight:400;font-size:18px;color:var(--cream);text-transform:uppercase}
.ins-card p{position:absolute;left:33px;width:220px;font-size:9.5px;line-height:16px;color:var(--text-light)}

/* lower dark */
.dark-bottom{position:absolute;left:0;top:2527px;width:1200px;height:1379px;background:linear-gradient(180deg,#2a1a0d 0%,#22160b 50%,#1a1109 100%)}
.partner{position:absolute;top:2719px;width:84px;height:84px;border-radius:50%;border:2px solid #6e4a2a;background:rgba(110,74,42,.18)}
.insta{position:absolute;top:2960px;width:224px;height:223px}

/* newsletter */
.news-input{left:306px;top:3351px;width:588px;height:41px;border-radius:21px;background:var(--white);border:2px solid var(--gold-2)}
.news-input span{position:absolute;left:22px;top:12px;font-size:9.5px;color:#555}
.news-input .btn{left:462px;top:3px;width:120px;height:31px;border-radius:16px}

/* footer */
.footer{left:0;top:3486px;width:1200px;height:420px;border-radius:40px 40px 0 0;background:#150e08}
.foot-col{position:absolute;top:3602px}
.foot-col h4{font-family:var(--serif);font-weight:500;font-size:12px;color:var(--gold);text-transform:uppercase;margin-bottom:11px}
.foot-col li{list-style:none;font-size:10px;line-height:19px;color:var(--text-light)}
.contact-row{display:flex;align-items:center;gap:8px;font-size:10px;line-height:19px}
.social{position:absolute;top:3704px;width:26px;height:26px;border-radius:50%;border:1px solid #555}
</style>
</head>
<body>

<div class="dark-top"></div>

<!-- header -->
<nav class="nav">
  <a style="left:318px">Products</a>
  <a style="left:384px">Custom Blend</a>
  <a style="left:475px">Wholesale</a>
  <a style="left:699px">Coffee &amp; Tea</a>
  <a style="left:784px">Partners</a>
  <a style="left:843px">Contact</a>
</nav>
<div class="brand">
  <div class="brand-dot"></div>
  <div class="brand-name">Husk<br>and<br>Kettle</div>
</div>
<div class="nav-icons">
  <svg width="11" height="11" viewBox="0 0 12 12" fill="none" stroke="#eee" stroke-width="1.3"><circle cx="5" cy="5" r="3.8"/><path d="M8 8l3 3"/></svg>
  <svg width="11" height="11" viewBox="0 0 12 12" fill="none" stroke="#eee" stroke-width="1.2"><circle cx="6" cy="4" r="2.6"/><path d="M1.5 11.5c.8-2.6 2.5-3.6 4.5-3.6s3.7 1 4.5 3.6"/></svg>
  <svg width="13" height="11" viewBox="0 0 14 12" fill="none" stroke="#eee" stroke-width="1.2"><path d="M1 1h2l1.5 7h7l1.5-5H4"/><circle cx="5.5" cy="10.5" r="1"/><circle cx="10.5" cy="10.5" r="1"/></svg>
</div>
<div class="abs" style="left:1043px;top:25px;width:10px;height:10px;border-radius:50%;background:#fff;color:#000;font-size:6px;text-align:center;line-height:10px">0</div>

<!-- hero -->
<div class="photo hero-photo" role="img" aria-label="Cup of coffee on a saucer surrounded by roasted coffee beans and burlap sacks"></div>
<h1 class="abs center h-serif hero-title">Artisan Coffee &amp; Tea, Your Way</h1>
<p class="abs center hero-sub">Discover our curated blends, customize your own coffee or tea, and indulge in luxury with every<br>sip. For enthusiasts and connoisseurs alike.</p>
<a class="btn" style="left:551px;top:249px;width:98px">Shop Now</a>

<!-- products -->
<h2 class="abs center h-serif sec-title" style="top:830px;color:var(--cream)">Artisan Coffee &amp; Tea, Your Way</h2>

<div class="card" style="left:147px">
  <div class="photo" role="img" aria-label="Roasted coffee beans in metal scoops" style="background:linear-gradient(160deg,#6a4a30,#3a2212 60%,#8a5a30)"></div>
  <h3>Brazilian Arabica</h3>
  <p>Smooth, nutty, chocolatey – perfect for daily indulgence.</p>
  <a class="btn">Add to Cart</a>
</div>
<div class="card" style="left:377px">
  <div class="photo" role="img" aria-label="Red coffee cherries on a branch with green leaves" style="background:linear-gradient(160deg,#3f6a2a,#a8261c 50%,#2f4a1f)"></div>
  <h3>Ethiopian Yirgach...</h3>
  <p>Floral and tea-like acidity with blueberry &amp; mocha notes.</p>
  <a class="btn">Add to Cart</a>
</div>
<div class="card" style="left:607px">
  <div class="photo" role="img" aria-label="Fresh green tea leaves in a woven basket" style="background:linear-gradient(160deg,#2d5a22,#4f8a34 50%,#6a4a2a)"></div>
  <h3>Darjeeling Green Tea</h3>
  <p>First flush, crisp, and refreshing with a delicate aroma.</p>
  <a class="btn">Add to Cart</a>
</div>
<div class="card" style="left:837px">
  <div class="photo" role="img" aria-label="Loose dried black tea leaves with a wooden scoop" style="background:linear-gradient(160deg,#4a4240,#221b18 55%,#6a4a30)"></div>
  <h3>Assam Black Tea</h3>
  <p>Full-bodied, rich, and malty – perfect for breakfast blends.</p>
  <a class="btn">Add to Cart</a>
</div>

<!-- create blend -->
<h2 class="abs center h-serif sec-title" style="top:1278px;color:var(--cream)">Create Your Own Blend</h2>
<p class="abs center" style="top:1331px;font-size:10px;line-height:16px">Choose your beans or leaves, select your roast or steep, and personalize your packaging.<br>Members enjoy advanced options and exclusive perks.</p>

<svg class="abs" style="left:380px;top:1385px" width="420" height="80" viewBox="0 0 420 80" fill="none" stroke="#8a5a26" stroke-width="1" stroke-dasharray="3 3">
  <path d="M14 48 C70 80 150 80 176 48"/>
  <path d="M262 46 C270 10 330 10 410 48"/>
</svg>

<div class="step" style="left:264px;top:1396px">
  <div class="step-circle">
    <svg class="abs" style="left:28px;top:26px" width="32" height="36" viewBox="0 0 32 36" fill="none" stroke="#fff" stroke-width="2"><path d="M8 30c-6-8-2-22 12-26 2 12-2 22-12 26z"/><path d="M10 32c8 0 16-4 18-12"/></svg>
    <div class="step-num">01</div>
  </div>
  <p>Select your coffee beans<br>or tea leaves.</p>
</div>
<div class="step" style="left:514px;top:1396px">
  <div class="step-circle">
    <svg class="abs" style="left:26px;top:26px" width="36" height="36" viewBox="0 0 36 36" fill="none" stroke="#fff" stroke-width="2"><circle cx="18" cy="18" r="13"/><path d="M18 9v10"/></svg>
    <div class="step-num">02</div>
  </div>
  <p>Choose your roast level or<br>steep style.</p>
</div>
<div class="step" style="left:749px;top:1396px">
  <div class="step-circle">
    <svg class="abs" style="left:28px;top:26px" width="32" height="34" viewBox="0 0 32 34" fill="#fff"><rect x="3" y="11" width="26" height="7" rx="1"/><rect x="5" y="19" width="22" height="13" rx="1"/><rect x="14" y="11" width="4" height="21" fill="#8a4a1a"/><path d="M16 11c-4-8-10-6-8-2 1 2 5 2 8 2zM16 11c4-8 10-6 8-2-1 2-5 2-8 2z"/></svg>
    <div class="step-num">03</div>
  </div>
  <p>Customize your packaging<br>or gift options.</p>
</div>
<a class="btn" style="left:539px;top:1557px;width:122px">Start Blending</a>

<!-- wholesale -->
<div class="photo wholesale" role="img" aria-label="Close-up of dark roasted coffee beans"></div>
<h2 class="abs center h-serif" style="top:1750px;font-size:32px;color:var(--white)">Wholesale &amp; Partnerships</h2>
<p class="abs center" style="top:1797px;font-size:10px;line-height:16px;color:var(--white)">Husk &amp; Kettle works with luxury lounges, hotels, and retailers. Access exclusive bulk pricing,<br>tailored blends, and premium service.</p>
<a class="btn" style="left:551px;top:1839px;width:98px">Add to Cart</a>

<!-- insights -->
<h2 class="abs center h-serif sec-title" style="top:2038px;color:var(--dark-text)">Coffee &amp; Tea Insights</h2>

<div class="ins-card" style="left:23px">
  <div class="photo" role="img" aria-label="Green coffee beans in a wooden bowl" style="inset:0;background:linear-gradient(180deg,#8a8560 0%,#5a5640 45%,#2a2a2a 100%)"></div>
  <h3 style="top:197px">Green Coffee Beans</h3>
  <p style="top:228px">Store cool, dry, and airtight. Optimal quality 6–12 months, shelf life up to 24 months.</p>
</div>
<div class="ins-card" style="left:313px">
  <div class="photo" role="img" aria-label="Loose black tea leaves spilling from a glass jar" style="inset:0;background:linear-gradient(180deg,#3a3330 0%,#231c18 50%,#3a2a20 100%)"></div>
  <h3 style="top:197px">Black Tea</h3>
  <p style="top:228px">Fully oxidized leaves retain flavor longer. Store in airtight tins in cool, dry environment.</p>
</div>
<div class="ins-card" style="left:604px">
  <div class="photo" role="img" aria-label="Tea being poured from a glass teapot into small cups on a teal table" style="inset:0;background:linear-gradient(180deg,#1f3e52 0%,#16707a 55%,#0f6a70 100%)"></div>
  <h3 style="top:197px">Steeping Guide</h3>
  <p style="top:228px">Perfect temperatures &amp; times for every type of coffee &amp; tea, from delicate green teas ...</p>
</div>
<div class="ins-card" style="left:895px;background:linear-gradient(135deg,#7a4316,#b0702e)">
  <h3 style="top:64px">Origins &amp; Notes</h3>
  <p style="top:93px">Interactive map planned showing regions, bean/leaf types, flavor profiles, and processing methods.</p>
  <div class="abs" style="left:36px;top:224px;width:30px;height:30px;border-radius:50%;background:#fff"></div>
  <svg class="abs" style="left:47px;top:233px" width="10" height="12" viewBox="0 0 10 12" fill="none" stroke="#333" stroke-width="1.6"><path d="M3 2l4 4-4 4"/></svg>
</div>

<!-- lower dark -->
<div class="dark-bottom"></div>

<h2 class="abs center h-serif sec-title" style="top:2634px;color:var(--cream)">Trusted by Distinguished Lounges</h2>
<div class="partner" style="left:243px"></div>
<div class="partner" style="left:368px"></div>
<div class="partner" style="left:492px"></div>
<div class="partner" style="left:618px"></div>
<div class="partner" style="left:747px"></div>
<div class="partner" style="left:871px"></div>

<h2 class="abs center h-serif sec-title" style="top:2893px;color:var(--cream)">Follow Us Instagram</h2>
<div class="photo insta" style="left:23px;background:linear-gradient(180deg,#3a2214,#6a3a1c 50%,#2a1a10)" role="img" aria-label="Tea poured from a copper kettle into a glass cup"></div>
<div class="photo insta" style="left:256px;background:linear-gradient(180deg,#b8b2a8,#3a4a7a 50%,#8a8a60)" role="img" aria-label="Tea cups with blue patterned saucers and a glass teapot"></div>
<div class="photo insta" style="left:490px;background:radial-gradient(circle at 50% 50%,#ece9e4 40%,#5a5a40 41%,#e6e2dc 60%,#3a3a3a)" role="img" aria-label="Steeped tea leaves on a white plate"></div>
<div class="photo insta" style="left:725px;background:linear-gradient(180deg,#5a3a22,#c89a40 60%,#3a2a1a)" role="img" aria-label="Golden tea poured into a glass pitcher"></div>
<div class="photo insta" style="left:959px;background:linear-gradient(180deg,#8a8480,#5a4a40 55%,#2a2420)" role="img" aria-label="Hands pouring tea from a glass pot"></div>

<!-- newsletter -->
<h2 class="abs center h-serif sec-title" style="top:3268px;color:var(--cream)">Subscribe to Our Newsletter</h2>
<p class="abs center" style="top:3316px;font-size:10px">Get updates on our weekly deals and seasonal specials. We promise you'll love our emails</p>
<div class="abs news-input"><span>Enter Your Email</span><a class="btn">Subscribe</a></div>

<!-- footer -->
<div class="abs footer"></div>
<div class="abs" style="left:198px;top:3614px;width:160px;text-align:center">
  <div style="width:44px;height:44px;border-radius:50%;background:var(--gold-2);margin:0 auto 10px"></div>
  <div style="font-family:var(--serif);font-size:28px;line-height:32px;color:var(--gold-2);text-transform:uppercase">Husk<br><span style="font-size:18px;line-height:22px">and</span><br>Kettle</div>
</div>

<div class="foot-col" style="left:457px">
  <h4>Quick Links</h4>
  <ul><li>Home</li><li>Shop</li><li>Custom Blends</li><li>Membership</li><li>Wholesale</li><li>About Us</li><li>Blog / Recipes</li><li>Contact</li></ul>
</div>
<div class="foot-col" style="left:625px">
  <h4>Information</h4>
  <ul><li>Search</li><li>About us</li><li>Locations &amp; Menu</li><li>Refund Policy</li><li>Privacy Policy</li></ul>
</div>
<div class="foot-col" style="left:813px">
  <h4>Contact Us</h4>
  <div class="contact-row"><svg width="9" height="8" viewBox="0 0 10 8" fill="none" stroke="#c07a3a"><rect x=".5" y=".5" width="9" height="7"/><path d="M.5.5l4.5 4 4.5-4"/></svg>support@huskandkettle.com</div>
  <div class="contact-row"><svg width="9" height="9" viewBox="0 0 10 10" fill="#c07a3a"><path d="M2 0l2 2.5-1 1.5c.6 1.3 1.7 2.4 3 3l1.5-1L10 8l-1.5 2C4.5 10 0 5.5 0 1.5z"/></svg>+1 (XXX) XXX-XXXX</div>
  <div class="contact-row"><svg width="8" height="10" viewBox="0 0 8 10" fill="#c07a3a"><path d="M4 0a4 4 0 0 1 4 4c0 3-4 6-4 6S0 7 0 4a4 4 0 0 1 4-4z"/><circle cx="4" cy="4" r="1.4" fill="#150e08"/></svg>123 Coffee Street, City, State, Zip</div>
</div>
<div class="social" style="left:814px" aria-label="Social profile one"></div>
<div class="social" style="left:848px" aria-label="Social profile two"></div>

<div class="abs" style="left:147px;top:3857px;width:906px;height:1px;background:#3a2c20"></div>
<div class="abs" style="left:1081px;top:3845px;width:26px;height:26px;border-radius:50%;background:var(--gold-2)"></div>
<svg class="abs" style="left:1089px;top:3853px" width="10" height="10" viewBox="0 0 10 10" fill="none" stroke="#fff" stroke-width="1.4"><path d="M2 6.5l3-3 3 3"/></svg>
<p class="abs center" style="top:3877px;font-size:10px;color:var(--text-light)">© Copyright 2026 Husk &amp; Kettle. All right reserved</p>

</body>
</html>
```